Stylish new business card needed!

Hello everyone! I am in need of a new business card design for an alarm company here in Hurricane WV. I have all fonts, color codes and logos provided for you use! We are a young company and like the style of a clean sleek looking business card. Would like it double sided, one side holding the logo and the other with your design!
Target Market(s)
The people that are looking for the newest tech for home automation and security
Industry/Entity Type
Alarm services; Home automation
Contact Information for Business Card
Name of person; position (Sales; Installer); Phone Number (555.418.7260); Employee cell Number; Website (www.GuardedByVelk.example); Employee Email; Double sided
Look and feel
Each slider illustrates characteristics of the customer's brand and the style your logo design should communicate.

```html
<!DOCTYPE html>
<html lang="en">
<head>
<meta charset="utf-8">
<title>Velk Business Card</title>
<link href="https://fonts.googleapis.com/css2?family=Arimo:wght@400;700&display=swap" rel="stylesheet">
<style>
  :root {
    --backdrop: #262628;
    --card: #1f1f23;
    --card-deep: #18181b;
    --orange: #f28c45;
    --grey: #9a9a9a;
    --white: #ffffff;
  }
  * { box-sizing: border-box; margin: 0; padding: 0; }
  html, body { width: 1200px; height: 780px; overflow: hidden; }
  body {
    background: var(--backdrop);
    font-family: "Arimo", Arial, sans-serif;
    display: flex;
    align-items: center;
    justify-content: center;
    gap: 40px;
  }
  .card {
    position: relative;
    width: 560px;
    height: 320px;
    border-radius: 22px;
    border: 3px solid var(--orange);
    overflow: hidden;
    background: var(--card);
  }

  /* Back side */
  .card--back { background: var(--card-deep); }
  .back-pattern {
    position: absolute; inset: 0;
    background: linear-gradient(160deg, #2a2a2e 0%, #151518 55%, #1c1c20 100%);
  }
  .back-name {
    position: absolute;
    right: 46px; top: 58px;
    font-weight: 700;
    font-size: 26px;
    color: var(--orange);
    letter-spacing: 1px;
  }

  /* Front side */
  .brand {
    position: absolute;
    left: 44px; top: 92px;
    width: 230px;
  }
  .brand-name {
    font-weight: 700;
    font-size: 72px;
    line-height: 1;
    color: var(--orange);
    letter-spacing: 2px;
  }
  .brand-tagline {
    margin-top: 12px;
    font-weight: 700;
    font-size: 10px;
    letter-spacing: 0.6px;
    text-transform: uppercase;
    color: var(--orange);
  }
  .divider {
    position: absolute;
    left: 282px; top: 60px;
    width: 2px; height: 170px;
    background: var(--white);
  }
  .contact {
    position: absolute;
    left: 306px; top: 56px;
    color: var(--white);
  }
  .contact-name {
    font-weight: 700;
    font-size: 26px;
    line-height: 1.05;
  }
  .contact-name .first { color: var(--orange); }
  .contact-role {
    font-weight: 700;
    font-size: 13px;
    margin-top: 4px;
  }
  .contact-list {
    list-style: none;
    margin-top: 22px;
    font-size: 12.5px;
    line-height: 1.55;
  }
  .contact-list li { display: flex; align-items: center; gap: 8px; }
  .contact-list svg { width: 12px; height: 12px; flex: none; }

  .footer-band {
    position: absolute;
    left: 0; right: 0; bottom: 16px;
    height: 40px;
  }
  .band-orange {
    position: absolute;
    left: 0; bottom: 0;
    width: 330px; height: 16px;
    background: var(--orange);
  }
  .band-name {
    position: absolute;
    left: 340px; bottom: -4px;
    font-weight: 700;
    font-size: 30px;
    color: var(--grey);
    letter-spacing: 1px;
  }
  .band-grey {
    position: absolute;
    left: 430px; right: 0; bottom: 22px;
    height: 16px;
    background: var(--grey);
  }
</style>
</head>
<body>

  <section class="card card--back" aria-label="Card back">
    <div class="back-pattern" role="img" aria-label="Repeating brand wordmark pattern in gloss black on matte black"></div>
    <div class="back-name">Velk</div>
  </section>

  <section class="card card--front" aria-label="Card front">
    <div class="brand">
      <div class="brand-name">Velk</div>
      <div class="brand-tagline">Automation and Security Services</div>
    </div>

    <div class="divider"></div>

    <div class="contact">
      <div class="contact-name"><span class="first">Mira</span> Holan</div>
      <div class="contact-role">Sales; Installer</div>
      <ul class="contact-list">
        <li>
          <svg viewBox="0 0 24 24" fill="var(--orange)"><path d="M6.6 10.8a15 15 0 0 0 6.6 6.6l2.2-2.2a1 1 0 0 1 1-.25 11.4 11.4 0 0 0 3.6.57 1 1 0 0 1 1 1V20a1 1 0 0 1-1 1A17 17 0 0 1 3 4a1 1 0 0 1 1-1h3.5a1 1 0 0 1 1 1c0 1.25.2 2.45.57 3.57a1 1 0 0 1-.25 1z"/></svg>
          555.418.7260
        </li>
        <li>
          <svg viewBox="0 0 24 24" fill="none" stroke="var(--white)" stroke-width="2"><rect x="6" y="2" width="12" height="20" rx="2"/></svg>
          555.902.3318
        </li>
        <li>
          <svg viewBox="0 0 24 24" fill="none" stroke="var(--orange)" stroke-width="2"><circle cx="12" cy="12" r="10"/><path d="M2 12h20M12 2a15 15 0 0 1 0 20M12 2a15 15 0 0 0 0 20"/></svg>
          www.GuardedByVelk.example
        </li>
        <li>
          <svg viewBox="0 0 24 24" fill="none" stroke="var(--orange)" stroke-width="2"><rect x="2" y="5" width="20" height="14" rx="2"/><path d="M2 6l10 7 10-7"/></svg>
          info@GuardedByVelk.example
        </li>
      </ul>
    </div>

    <div class="footer-band">
      <div class="band-orange"></div>
      <div class="band-name">Velk</div>
      <div class="band-grey"></div>
    </div>
  </section>

</body>
</html>
```